Oral Surgeon Referral Pads

Hello. We need referral pads for Dr Elsabet Quorvane, DDS board certified oral surgeon's new office - Harrowgate Dunmere Oral & Maxillofacial Surgery. See logo uploaded. See some images we would like included
Updates

Designs look the same

Font styles to use
Serif
Script

Colors
00AB8E
00BBA5
67D7C9
C6EFE9
E9F9F6

Requirements
Must have
• Color Pantone 623c. Also foldable business cards

```html
<!DOCTYPE html>
<html lang="en">
<head>
<meta charset="utf-8">
<title>Referral Pad – Harrowgate Dunmere Oral &amp; Maxillofacial Surgery</title>
<link href="https://fonts.googleapis.com/css2?family=Open+Sans:wght@300;400;600;700&family=Source+Sans+3:wght@400;600&family=Roboto+Condensed:wght@700&family=Lora:wght@500&display=swap" rel="stylesheet">
<style>
  :root {
    --stage: #636363;
    --paper: #ffffff;
    --navy: #1f2d6b;
    --rule: #213a7c;
    --band: #1f2b5f;
    --ink: #1a1a1a;
    --title: #ffffff;
    --chart-a: #fde9e1;
    --chart-b: #f7c4a8;
    --chart-c: #e3f2fb;
  }
  * { box-sizing: border-box; margin: 0; padding: 0; }
  html, body { width: 1200px; height: 1004px; overflow: hidden; }
  body {
    background: var(--stage);
    font-family: "Open Sans", Arial, sans-serif;
    position: relative;
  }
  .set-title {
    position: absolute; top: 34px; left: 0; width: 1200px;
    text-align: center; color: var(--title);
    font-weight: 300; font-size: 46px; line-height: 1.2;
  }
  .page {
    position: absolute; top: 156px; width: 506px; height: 708px;
    background: var(--paper); overflow: hidden;
    box-shadow: 0 4px 10px rgba(0,0,0,.35);
  }
  .page--front { left: 74px; }
  .page--back { left: 619px; }
  .page__band {
    position: absolute; left: 0; right: 0; bottom: 0; height: 16px;
    background: var(--band);
  }
  .page--back .page__band { height: 12px; }
  .t { position: absolute; white-space: nowrap; color: var(--navy); }

  /* front */
  .doctor { font-weight: 700; font-size: 15px; }
  .contact { font-size: 12.2px; display: flex; align-items: center; gap: 6px; }
  .contact svg { width: 11px; height: 11px; fill: var(--navy); }
  .brand {
    left: 226px; width: 268px; text-align: center; color: var(--navy);
    font-family: "Lora", Georgia, serif; font-weight: 500; font-style: normal;
  }
  .brand__name { top: 86px; font-size: 24px; line-height: 30px; }
  .brand__sub { top: 120px; font-size: 16px; line-height: 22px; }
  .brand__mark {
    position: absolute; left: 333px; top: 20px; width: 54px; height: 54px;
    border: 2px solid var(--navy); border-radius: 50%;
  }
  .field { font-size: 12.2px; }
  .rule { position: absolute; left: 22px; width: 459px; height: 1.5px; background: var(--rule); }
  .blank { position: absolute; height: 1.5px; background: var(--rule); }
  .heading { font-weight: 600; font-size: 11.5px; }
  .heading--lg { font-size: 13.5px; }
  .chk { display: flex; align-items: center; gap: 6px; font-size: 13.2px; }
  .chk--bold { font-weight: 600; font-size: 11.8px; }
  .box { width: 8px; height: 8px; border: 1.4px solid var(--navy); flex: none; }

  /* back */
  .intro { font-size: 12.2px; color: var(--ink); left: 24px; }
  .anatomy-title {
    left: 0; width: 506px; text-align: center; color: #000;
    font-family: "Roboto Condensed", "Arial Narrow", sans-serif; font-weight: 700; font-size: 19px;
  }
  .anatomy-chart {
    position: absolute; left: 93px; top: 95px; width: 322px; height: 172px;
    background: linear-gradient(135deg, var(--chart-a) 0%, var(--chart-b) 45%, var(--chart-c) 100%);
    border-radius: 4px;
  }
  .notes {
    position: absolute; left: 23px; color: var(--ink);
    font-family: "Source Sans 3", Arial, sans-serif; font-weight: 600;
    font-size: 10px; line-height: 15.7px; white-space: nowrap;
  }
</style>
</head>
<body>
  <div class="set-title">Change 05</div>

  <section class="page page--front">
    <div class="t doctor" style="left:22px;top:37px;">Dr Elsabet Quorvane</div>

    <div class="t contact" style="left:22px;top:80px;">
      <svg viewBox="0 0 12 12"><path d="M6 0a4 4 0 0 0-4 4c0 3 4 8 4 8s4-5 4-8a4 4 0 0 0-4-4zm0 5.6A1.6 1.6 0 1 1 6 2.4a1.6 1.6 0 0 1 0 3.2z"/></svg>
      Your address, City State, Zip 1234</div>
    <div class="t contact" style="left:22px;top:98px;">
      <svg viewBox="0 0 12 12"><path d="M2.4 1l2 2.2-1 1.3a7 7 0 0 0 3.9 3.9l1.3-1 2.2 2-1.3 1.6C5.6 11 1 6.4 1 2.3z"/></svg>
      123 456 789</div>
    <div class="t contact" style="left:22px;top:116px;">
      <svg viewBox="0 0 12 12"><path d="M3 1h5v3H3zM1 5h10v6H1zm2 1.5v1h2v-1zm0 2v1h2v-1zm4-2v1h2v-1zm0 2v1h2v-1z"/></svg>
      123 456 789</div>
    <div class="t contact" style="left:22px;top:134px;">
      <svg viewBox="0 0 12 12"><path d="M1 4l5-3 5 3v7H1zm1.2.6L6 7l3.8-2.4L6 2.3z"/></svg>
      info@yourclinicmail.com</div>

    <span class="brand__mark" aria-hidden="true"></span>
    <div class="t brand brand__name">Harrowgate Dunmere</div>
    <div class="t brand brand__sub">Oral &amp; Maxillofacial Surgery</div>

    <div class="t field" style="left:22px;top:169px;">Today’ s Date&nbsp;&nbsp; DD &nbsp;&nbsp;&nbsp; / &nbsp;&nbsp;&nbsp;&nbsp; MM &nbsp;&nbsp;&nbsp; / &nbsp;&nbsp;&nbsp;YYY</div>
    <div class="rule" style="top:195px;"></div>
    <div class="t field" style="left:22px;top:204px;">Patient’ s Name</div>
    <div class="rule" style="top:228px;"></div>
    <div class="t field" style="left:22px;top:236px;">Patient’ Phone Number</div>
    <div class="rule" style="top:260px;"></div>
    <div class="t field" style="left:22px;top:265px;">Referred by</div>
    <div class="rule" style="top:288px;"></div>
    <div class="t field" style="left:23px;top:297px;">Additional Comments</div>

    <div class="t heading" style="left:59px;top:333px;">PROCEDURE</div>
    <div class="t chk chk--bold" style="left:60px;top:353px;"><span class="box"></span>Extraction</div>
    <div class="t chk chk--bold" style="left:145px;top:352px;"><span class="box"></span>Implants</div>
    <div class="t chk chk--bold" style="left:231px;top:353px;"><span class="box"></span>Consultation</div>
    <div class="t chk chk--bold" style="left:323px;top:352px;"><span class="box"></span>Radiogrphs</div>

    <div class="t chk" style="left:22px;top:393px;"><span class="box"></span>Wisdom Teeth</div>
    <div class="t chk" style="left:22px;top:411px;"><span class="box"></span>Extraction</div>
    <div class="t chk" style="left:22px;top:429px;"><span class="box"></span>Implants</div>
    <div class="t chk" style="left:22px;top:447px;"><span class="box"></span>Bone Grafing</div>
    <div class="t chk" style="left:22px;top:464px;"><span class="box"></span>Exposure and bonding</div>
    <div class="t chk" style="left:22px;top:482px;"><span class="box"></span>Biopsy(SOFT or Hard Tissue)</div>

    <div class="t chk" style="left:230px;top:393px;"><span class="box"></span>Lesion Evaluation</div>
    <div class="t chk" style="left:230px;top:411px;"><span class="box"></span>Infection (I&amp;D</div>
    <div class="t chk" style="left:230px;top:429px;"><span class="box"></span>Alveoloplasty</div>
    <div class="t chk" style="left:230px;top:447px;"><span class="box"></span>Frenectomy</div>
    <div class="t chk" style="left:230px;top:464px;"><span class="box"></span>Orthognathic</div>
    <div class="t chk" style="left:230px;top:482px;"><span class="box"></span>TMJ</div>
    <div class="t chk" style="left:230px;top:500px;"><span class="box"></span>Other</div>
    <div class="blank" style="left:244px;width:70px;top:525px;"></div>
    <div class="blank" style="left:244px;width:70px;top:543px;"></div>

    <div class="t chk" style="left:356px;top:393px;">Implants</div>
    <div class="t chk" style="left:349px;top:410px;"><span class="box"></span>Veltrane</div>
    <div class="t chk" style="left:349px;top:428px;"><span class="box"></span>Osterline</div>
    <div class="t chk" style="left:349px;top:446px;"><span class="box"></span>Other</div>
    <div class="blank" style="left:362px;width:70px;top:473px;"></div>
    <div class="blank" style="left:362px;width:70px;top:492px;"></div>

    <div class="t heading heading--lg" style="left:59px;top:548px;">Surgical Template</div>
    <div class="t chk" style="left:22px;top:568px;"><span class="box"></span>To be provided by Restorative dentist</div>
    <div class="t chk" style="left:286px;top:568px;"><span class="box"></span>To be fabricated by the surgeon</div>
    <div class="t chk" style="left:22px;top:586px;"><span class="box"></span>Other</div>
    <div class="blank" style="left:91px;width:170px;top:601px;"></div>

    <div class="t heading heading--lg" style="left:59px;top:616px;">Radfographs</div>
    <div class="t chk" style="left:22px;top:634px;"><span class="box"></span>Being Mafled/emafled</div>
    <div class="t chk" style="left:182px;top:634px;"><span class="box"></span>Given to the Patient</div>
    <div class="t chk" style="left:342px;top:634px;"><span class="box"></span>Please Take</div>
    <div class="t chk" style="left:22px;top:652px;"><span class="box"></span>Other</div>
    <div class="blank" style="left:91px;width:170px;top:665px;"></div>

    <div class="page__band"></div>
  </section>

  <section class="page page--back">
    <div class="t intro" style="top:19px;">You can save time by going online.Register and update your health today</div>
    <div class="t anatomy-title" style="top:61px;">TEETH ANATOMY</div>
    <div class="anatomy-chart" role="img" aria-label="Labelled illustration of upper and lower jaw teeth anatomy: incisors, fangs, premolars and molars"></div>

    <div class="notes" style="top:285px;">Patient Instructions</div>

    <div class="notes" style="top:317px;">PLEASE NOTE THAT IN MOST INSTANCES THE PATENT IS FIRST SEEN FOR CONSULATION TO REVEW<br>THE HEALTH HISTORY; DECIDE ON THE MOST APPROPRIATE ANESTHESIAAND TREATMENT PLAN,<br>AND SCHEDULE THE SURGERY AT A SEPARATE APPONTMENT.</div>

    <div class="notes" style="top:381px;">Please Assist us by having the following infomation avaliable with you at the time of appoint.</div>

    <div class="notes" style="top:414px;left:21px;">Ment: Your surgical referral sup and any x-rays if applicable, a list ofmedicatioins, insurance<br>policy infomation</div>

    <div class="notes" style="top:465px;">Wportant: All patients unmarried or under the age of 19 must be accompanied by a paremt or<br>guardian during the Consulation and Trcatment visits.</div>

    <div class="notes" style="top:515px;">SPECIAL INSTRUCTIONS FOR PATIENTS HAVING I.V SEDATOPN / GENERAL ANESTHESIA:<br>&nbsp;&nbsp;&nbsp;&nbsp;&nbsp;- NO FOOD OR DRINK (including Water) AT LEAST 6 HPURS [ROPR TP YPUR SURGERY UNLESS<br>OTHERWISE INDICATED BY THE SURGEON. Some medicaitons may be continuedand this will be<br>discussed at your consulation.</div>

    <div class="notes" style="top:598px;">&nbsp;&nbsp;&nbsp;&nbsp;&nbsp;. A responsible aduit must accompany you and REMAIN in the offer during the entire<br>treatment. They must alslo be able to drive you home. YOU cannot drive until the next day.<br>&nbsp;&nbsp;&nbsp;&nbsp;&nbsp;&nbsp;&nbsp;.Eat a light and easily digestible meal the night before the procedure. Do not drink any<br>alcoholife bevefages the night.before<br>&nbsp;&nbsp;&nbsp;&nbsp;&nbsp;&nbsp;.Wear comfortable clothing with sleeves which are easy to push up.</div>

    <div class="page__band"></div>
  </section>
</body>
</html>
```